Tech business card design

We need an amazing business card design for our new business 'Pexla' a marketing tech startup based in Sydney, Australia. We provide an online marketplace for businesses to search and buy advertising media, connect with service providers and learn more about marketing. We wish to communicate 'cool tech', reliability and professionalism and design based around our logo.

Target Market(s)

Business Owners

Contact Information for Business Card

Name
Position
Email Address
Website
Phone Number

Font styles to use
Other font styles liked:
• Avenir & Avenir Next

Colors

Designer to choose colors to be used in the design.

```html
<!DOCTYPE html>
<html lang="en">
<head>
<meta charset="utf-8">
<title>Pexla Business Card</title>
<link rel="stylesheet" href="https://fonts.googleapis.com/css2?family=Nunito+Sans:wght@400;700;800;900&display=swap">
<style>
  :root {
    --navy: #141a3d;
    --navy-deep: #0f1433;
    --navy-soft: #222a55;
    --ink: #1a1a1a;
    --muted: #555a66;
    --paper: #ffffff;
    --backdrop: #f4f4f4;
  }
  html, body {
    margin: 0;
    padding: 0;
    width: 1200px;
    height: 896px;
    overflow: hidden;
    background: var(--backdrop);
    font-family: "Nunito Sans", Arial, sans-serif;
  }
  .canvas {
    position: relative;
    width: 1200px;
    height: 896px;
  }
  .card {
    position: absolute;
    box-sizing: border-box;
  }
  .card-back {
    left: 165px;
    top: 170px;
    width: 304px;
    height: 533px;
    border-radius: 28px;
    background: var(--navy-deep);
    overflow: hidden;
  }
  .back-pattern {
    position: absolute;
    inset: 0;
    background: linear-gradient(180deg, var(--navy-soft) 0%, var(--navy-deep) 100%);
  }
  .back-brand {
    position: absolute;
    left: 0;
    right: 0;
    top: 628px;
    top: 456px;
    text-align: center;
    color: var(--paper);
    font-size: 38px;
    font-weight: 800;
    letter-spacing: -0.5px;
    line-height: 1;
  }
  .card-front {
    left: 533px;
    top: 310px;
    width: 515px;
    height: 295px;
    border-radius: 30px;
    background: var(--paper);
    border: 1px solid #dddddd;
  }
  .person-name {
    position: absolute;
    left: 19px;
    top: 22px;
    margin: 0;
    font-size: 20px;
    font-weight: 800;
    color: var(--navy);
    letter-spacing: 0.3px;
    line-height: 1.1;
  }
  .person-role {
    position: absolute;
    left: 19px;
    top: 48px;
    margin: 0;
    font-size: 14px;
    color: var(--muted);
    line-height: 1.2;
  }
  .front-brand {
    position: absolute;
    left: 16px;
    top: 186px;
    font-size: 80px;
    font-weight: 900;
    color: var(--navy);
    letter-spacing: -2px;
    line-height: 1;
  }
  .divider {
    position: absolute;
    left: 256px;
    top: 215px;
    width: 2px;
    height: 80px;
    background: var(--navy);
  }
  .contact {
    position: absolute;
    left: 276px;
    top: 211px;
    margin: 0;
    padding: 0;
    list-style: none;
    color: var(--ink);
  }
  .contact li { line-height: 1.25; }
  .contact-phone { font-size: 19px; font-weight: 700; }
  .contact-email { font-size: 14px; }
  .contact-web { font-size: 14px; font-weight: 700; }
</style>
</head>
<body>
<main class="canvas">
  <section class="card card-back" aria-label="Card back">
    <div class="back-pattern" role="img" aria-label="Repeating brand-name pattern in dark navy tones"></div>
    <div class="back-brand">Pexla</div>
  </section>

  <section class="card card-front" aria-label="Card front">
    <h1 class="person-name">MARCUS VALE</h1>
    <p class="person-role">Managing Director</p>
    <div class="front-brand">Pexla</div>
    <div class="divider"></div>
    <ul class="contact">
      <li class="contact-phone">000-123-4567</li>
      <li class="contact-email">info@pexlamail.com</li>
      <li class="contact-web">www.pexla.com</li>
    </ul>
  </section>
</main>
</body>
</html>
```